Home Remodeling company needs a business card design

we need a business card design for home remodeling company in hamilton county, indiana USA. we offers a wide range of construction services including whole house renovations, Design and Build Basements and Kitchen and Bathroom Remodeling . we would like to see designs for both site of business card that use the same color of the company logo and also including all information below :
1- Karim Feltous CEO / General Contractor
2- all company contacts Telephone numbers ( 1-888-DULOM-47 ) ( 317-555-0193) email address ( info@dulomhome.com) website ( www.dulomhome.com ) and social media logos (Facebook- twitter- google plus )
3- company logo
4- licensed . insured . bonded

```html
<!DOCTYPE html>
<html lang="en">
<head>
<meta charset="utf-8">
<title>Dulom Home Remodeling – Business Card</title>
<link rel="stylesheet" href="https://fonts.googleapis.com/css2?family=Cabin:wght@400;500;600;700&display=swap">
<style>
  :root {
    --backdrop: #8d8d8f;
    --card-front: #e9e9eb;
    --card-back: #323234;
    --ink: #333335;
    --accent-red: #b0202b;
    --mark-grey: #5a5a5c;
    --back-light: #e7e7e7;
    --back-muted: #9a9a9c;
  }
  * { margin: 0; padding: 0; box-sizing: border-box; }
  html, body { width: 1105px; height: 1200px; overflow: hidden; }
  body {
    background: var(--backdrop);
    font-family: "Cabin", "Gill Sans", sans-serif;
    position: relative;
  }
  .card {
    position: absolute;
    left: 182px;
    width: 747px;
    height: 425px;
  }
  .card-front { top: 120px; background: var(--card-front); color: var(--ink); }
  .card-back  { top: 637px; background: var(--card-back); color: var(--back-light); }

  /* front */
  .person { position: absolute; left: 58px; top: 44px; }
  .person-name { font-size: 26px; font-weight: 600; letter-spacing: 0.2px; }
  .person-title { font-size: 20px; color: var(--accent-red); margin-top: 2px; }

  .contact-list { position: absolute; left: 59px; top: 164px; list-style: none; }
  .contact-item {
    display: flex; align-items: center; height: 29px;
    font-size: 19px; color: var(--ink);
  }
  .contact-icon { width: 17px; height: 17px; margin-right: 15px; fill: var(--ink); }

  .brand { position: absolute; left: 59px; top: 290px; }
  .brand-row { display: flex; align-items: center; }
  .brand-square { width: 14px; height: 14px; background: var(--accent-red); margin-right: 12px; }
  .brand-name {
    font-size: 56px; font-weight: 700; line-height: 1;
    letter-spacing: 2px; color: var(--ink);
  }
  .brand-tagline {
    font-size: 19px; letter-spacing: 6.2px; color: var(--mark-grey);
    margin-top: 6px; padding-left: 1px;
  }

  /* back */
  .back-brand {
    position: absolute; left: 0; right: 0; top: 150px;
    display: flex; justify-content: center; align-items: center;
  }
  .back-square { width: 30px; height: 30px; background: var(--back-light); margin-right: 16px; }
  .back-name { font-size: 58px; font-weight: 700; letter-spacing: 3px; line-height: 1; color: var(--back-light); }

  .credentials {
    position: absolute; left: 0; right: 0; top: 319px;
    text-align: center; font-size: 21px; letter-spacing: 0.4px;
  }
  .social-row {
    position: absolute; left: 0; right: 0; top: 361px;
    display: flex; justify-content: center; align-items: center;
  }
  .social-rule { width: 58px; height: 1px; background: var(--back-muted); }
  .social-dot {
    width: 26px; height: 26px; border-radius: 50%;
    background: var(--back-light); margin: 0 3px;
  }
  .social-rule.left { margin-right: 6px; }
  .social-rule.right { margin-left: 6px; }
</style>
</head>
<body>

<section class="card card-front" aria-label="Business card front">
  <div class="person">
    <p class="person-name">Karim Feltous</p>
    <p class="person-title">CEO / General Contractor</p>
  </div>

  <ul class="contact-list">
    <li class="contact-item">
      <svg class="contact-icon" viewBox="0 0 24 24" aria-hidden="true"><path d="M6.6 10.8a15.1 15.1 0 0 0 6.6 6.6l2.2-2.2c.3-.3.7-.4 1-.2 1.1.4 2.3.6 3.6.6.6 0 1 .4 1 1V20c0 .6-.4 1-1 1A17 17 0 0 1 3 4c0-.6.4-1 1-1h3.5c.6 0 1 .4 1 1 0 1.3.2 2.5.6 3.6.1.3 0 .7-.2 1z"/></svg>
      1-888-DULOM-47
    </li>
    <li class="contact-item">
      <svg class="contact-icon" viewBox="0 0 24 24" aria-hidden="true"><path d="M7 1h10a2 2 0 0 1 2 2v18a2 2 0 0 1-2 2H7a2 2 0 0 1-2-2V3a2 2 0 0 1 2-2zm0 3v14h10V4zm5 15.5a1.2 1.2 0 1 0 0 2.4 1.2 1.2 0 0 0 0-2.4z"/></svg>
      317-555-0193
    </li>
    <li class="contact-item">
      <svg class="contact-icon" viewBox="0 0 24 24" aria-hidden="true"><path d="M2 5h20v14H2zm2 2v.5l8 5 8-5V7zm0 2.8V17h16V9.8l-8 5z"/></svg>
      info@dulomhome.com
    </li>
    <li class="contact-item">
      <svg class="contact-icon" viewBox="0 0 24 24" aria-hidden="true"><path d="M12 2a10 10 0 1 0 0 20 10 10 0 0 0 0-20zm-1 17.9A8 8 0 0 1 4.1 11l4.9 5v1a2 2 0 0 0 2 2zm6.9-2.5A2 2 0 0 0 16 16h-1v-3a1 1 0 0 0-1-1H8v-2h2a1 1 0 0 0 1-1V7h2a2 2 0 0 0 2-2v-.4a8 8 0 0 1 2.9 12.8z"/></svg>
      www.dulomhome.com
    </li>
  </ul>

  <div class="brand">
    <div class="brand-row">
      <span class="brand-square" aria-hidden="true"></span>
      <span class="brand-name">DULOM</span>
    </div>
    <p class="brand-tagline">HOME REMODELING</p>
  </div>
</section>

<section class="card card-back" aria-label="Business card back">
  <div class="back-brand">
    <span class="back-square" aria-hidden="true"></span>
    <span class="back-name">DULOM</span>
  </div>
  <p class="credentials">LICENSED | INSURED | BONDED</p>
  <div class="social-row" aria-label="Social media links">
    <span class="social-rule left"></span>
    <span class="social-dot"></span>
    <span class="social-dot"></span>
    <span class="social-dot"></span>
    <span class="social-rule right"></span>
  </div>
</section>

</body>
</html>
```